Dietitian needs awesome business card

I need a contemporary design that's eye catching but professional.
My card is to given to doctors, specialists and patients alike.
I manage patients with chronic diseases
I have uploaded my logo and current business card, I would also like the other Certified Clinical Nutritionist logo incorporated into the design

Target Market(s)

Doctors, specialists and patients

Industry/Entity Type

Healthcare

Contact Information for Business Card

www.brightfieldnutrition.com.au
Ph: 0427 561 903
Fax: 6457 2183
email: marcus.k.diet@fernmail.com
Space on the back of the card with: Appointment date, Appointment time and appointment location

Font styles to use
Serif

Colors
fbee3e
876aae
ffc214

Requirements
Must have
• My Logo
• Certified Clinical Nutritionist Logo
• My 4 locations - Pinebrook Medical Centre, North Corrin Health, Hollis Medical, Ashcombe Doctors Surgery
Nice to have
• I like the colours in my current business card

```html
<!DOCTYPE html>
<html lang="en">
<head>
<meta charset="utf-8">
<title>Brightfield Nutrition &amp; Dietetics – Business Card</title>
<link href="https://fonts.googleapis.com/css2?family=Source+Sans+3:ital,wght@0,400;0,600;1,600&display=swap" rel="stylesheet">
<style>
  :root {
    --bg-top: #2b2b2b;
    --bg-bottom: #050505;
    --card: #ffffff;
    --brand-blue: #1f3f9a;
    --brand-blue-deep: #1a2f86;
    --brand-green: #8cc63f;
    --brand-green-bright: #b5d81c;
    --ink: #222222;
    --accent-orange: #f26522;
    --rule: #555555;
  }
  * { margin: 0; padding: 0; box-sizing: border-box; }
  html, body { width: 1200px; height: 900px; overflow: hidden; }
  body {
    position: relative;
    background: linear-gradient(180deg, var(--bg-top) 0%, #161616 55%, var(--bg-bottom) 100%);
    font-family: "Source Sans 3", "Myriad Pro", Arial, sans-serif;
    color: var(--ink);
  }
  .card {
    position: absolute;
    top: 306px;
    height: 271px;
    background: var(--card);
    border-radius: 12px;
    overflow: hidden;
    box-shadow: 0 2px 8px rgba(0,0,0,0.5);
  }
  .card--front { left: 149px; width: 439px; }
  .card--back { left: 608px; width: 441px; }

  /* brand */
  .brand { position: absolute; left: 94px; top: 16px; display: flex; align-items: center; gap: 10px; }
  .brand__dot { width: 72px; height: 72px; border-radius: 50%; background: var(--brand-blue); }
  .brand__name { color: var(--brand-blue); font-weight: 600; font-size: 26px; line-height: 1.05; }
  .brand__name span { display: block; font-size: 17px; }

  .contact {
    position: absolute; left: 0; width: 438px; top: 119px;
    text-align: center;
  }
  .contact__name { color: var(--brand-green); font-weight: 600; font-size: 15px; line-height: 18px; }
  .contact__role { font-size: 12.5px; line-height: 16px; margin-bottom: 7px; }
  .contact__line { font-size: 12.5px; line-height: 16px; }
  .contact__tagline {
    margin-top: 5px;
    color: var(--brand-green); font-style: italic; font-weight: 600; font-size: 12px;
    white-space: nowrap;
  }

  .band { position: absolute; top: 0; height: 100%; width: 50px; }
  .band--front {
    right: 0;
    background: linear-gradient(180deg, var(--brand-blue-deep) 0%, #2e6fc0 55%, var(--brand-green) 80%, var(--brand-green-bright) 100%);
  }
  .band--back {
    left: 0;
    background: linear-gradient(180deg, var(--brand-green) 0%, var(--brand-green-bright) 100%);
  }

  .locations { position: absolute; left: 68px; top: 52px; width: 140px; list-style: none; }
  .locations__item { font-size: 11.5px; line-height: 22px; color: var(--brand-blue); white-space: nowrap; }

  .appointment { position: absolute; left: 224px; top: 48px; width: 197px; }
  .appointment__row { display: flex; align-items: baseline; font-size: 13px; height: 32px; }
  .appointment__fill { flex: 1; margin-left: 3px; border-bottom: 1px dotted var(--rule); }

  .credential { position: absolute; left: 224px; top: 175px; display: flex; gap: 42px; }
  .credential__text { color: var(--accent-orange); font-size: 13px; line-height: 15.5px; }
  .credential__badge { width: 38px; height: 42px; margin-top: 2px; background: var(--accent-orange); }
</style>
</head>
<body>
  <section class="card card--front" aria-label="Card front">
    <div class="brand">
      <div class="brand__dot"></div>
      <div class="brand__name">Brightfield<span>Nutrition &amp; Dietetics</span></div>
    </div>
    <div class="contact">
      <p class="contact__name">Marcus Kellan</p>
      <p class="contact__role">Managing Director</p>
      <p class="contact__line">0427 561 903</p>
      <p class="contact__line">6457 2183</p>
      <p class="contact__line">marcus.k.diet@fernmail.com</p>
      <p class="contact__line">www.brightfieldnutrition.com.au</p>
      <p class="contact__tagline">Certified Clinical Nutritionist, Dietitian and Chef</p>
    </div>
    <div class="band band--front"></div>
  </section>

  <section class="card card--back" aria-label="Card back">
    <div class="band band--back"></div>
    <ul class="locations">
      <li class="locations__item">Pinebrook Medical Centre</li>
      <li class="locations__item">North Corrin Health</li>
      <li class="locations__item">Hollis Medical</li>
      <li class="locations__item">Ashcombe Doctors Surgery</li>
    </ul>
    <div class="appointment">
      <div class="appointment__row">Date:<span class="appointment__fill"></span></div>
      <div class="appointment__row">Time:<span class="appointment__fill"></span></div>
      <div class="appointment__row">Location:<span class="appointment__fill"></span></div>
    </div>
    <div class="credential">
      <p class="credential__text">Certified<br>Clinical<br>Nutritionist</p>
      <div class="credential__badge" role="img" aria-label="Certification badge"></div>
    </div>
  </section>
</body>
</html>
```